Fitness Equipment & Service

I want to make the card eye catching and fun. We are called Corvane Motion Limited and we are based in Wales. We sell, install and service all types of fitness equipment from Skipping ropes, right through the Dumbbells, Kettle bells and Barbells through to state of the art Treadmills, Running Machines and Strength Equipment. We also design and install changing room furniture and lockers.

TYPOGRAPHY
We would like to use Futrura. Futura has an appearance of efficiency and forwardness. The typeface is derived
from simple geometric forms (near-perfect circles, triangles and squares) and is based on strokes of
near-even weight, which are low in contrast. This is most visible in the almost perfectly round stroke of
the o, which is nonetheless slightly ovoid.
The lowercase has tall ascenders, which rise above the cap line. The uppercase
characters present proportions similar to those of classical Roman capitals.

TYPOGRAPHIC CONSIDERATIONS
No Strike though
No Horizontal Scaling
No Drop Shadows
No Effects
Never use less than 120% Leading

OUR CORPORATE COLOURS
BRAND GUIDELINES
We were thinking that our primary colour palette consists of the Acid Green (Pantone 382) and Process Black.

We work closely with tquarly Ltd and would like to include their name on the card somewhere. I have attached images of the other brands that we work with as an idea or the small icons I have included that illustrate what we do?. I have very kindly been given permission to use any of the images off the files that I have included below, so I hope these help. I will include these below. I would be open to suggestions if it made the card more striking Can you do it?
Updates

Hi All, Just wanted to add a few thoughts but you are the guys with the creative visions (thats why are here) We are based in Wales, UK and we would be open to lots of different ideas on a theme but must be eye catching, Bold and FUN. If you can or think that the Welsh or any dragon could be put in there then go for it (its not a must have) We have also added some ideas for colour but again its over to you!! GO FOR IT ! Thanks and look forward to your visions! Owen

Hi All, Just thought I would sen through the contact details that need to be on the card. (if you want to play around with icons instead of the wording twitter, Facebook, go for it): Corvane Motion Limited Owen Pritchard Managing Director Mob: +44 (0)7582 913 406 e-mail: sales@corvanemotion.co.uk Web: Corvanemotion.co.uk twitter: @motionLetterbin Facebook: Corvane Motion Limited

```html
<!DOCTYPE html>
<html lang="en">
<head>
<meta charset="utf-8">
<title>Corvane Motion Limited – Business Card</title>
<link rel="stylesheet" href="https://fonts.googleapis.com/css2?family=Jost:wght@400;500;600&display=swap">
<style>
  :root {
    --page: #e9e8e4;
    --card-white: #ffffff;
    --card-grey: #e6e7e9;
    --map-tone: #e2e4e6;
    --black: #111111;
    --band-top: #2a2a2a;
    --band-bottom: #0d0d0d;
    --acid: #c4d600;
    --ink-light: #ffffff;
    --ink-soft: #e6e6e6;
    --shadow: rgba(0, 0, 0, 0.18);
  }
  * { box-sizing: border-box; margin: 0; padding: 0; }
  html, body {
    width: 1200px;
    height: 950px;
    overflow: hidden;
    background: var(--page);
    font-family: "Jost", "Futura", sans-serif;
  }
  .sheet {
    width: 1200px;
    height: 950px;
    display: flex;
    flex-direction: column;
    align-items: center;
    justify-content: center;
    gap: 44px;
  }
  .card {
    position: relative;
    width: 720px;
    height: 412px;
    border-radius: 4px;
    overflow: hidden;
    box-shadow: 0 8px 24px var(--shadow);
  }

  /* Back of card */
  .card--back {
    background: linear-gradient(160deg, var(--card-white) 0%, var(--card-grey) 100%);
    display: flex;
    flex-direction: column;
    align-items: center;
    justify-content: center;
    gap: 22px;
  }
  .brand-disc {
    width: 112px;
    height: 112px;
    border-radius: 50%;
    background: var(--acid);
  }
  .brand-name--back {
    font-weight: 500;
    font-size: 24px;
    line-height: 1.25;
    letter-spacing: 0.08em;
    color: var(--black);
    text-align: center;
    text-transform: uppercase;
  }

  /* Front of card */
  .card--front { background: var(--card-white); }
  .world-map {
    position: absolute;
    inset: 0 0 auto 0;
    height: 230px;
    background: radial-gradient(ellipse at 60% 45%, var(--map-tone) 0%, rgba(226,228,230,0.5) 55%, var(--card-white) 100%);
  }
  .brand-name--front {
    position: absolute;
    top: 82px;
    left: 300px;
    font-weight: 500;
    font-size: 30px;
    line-height: 1.2;
    letter-spacing: 0.06em;
    color: var(--black);
    text-transform: uppercase;
  }
  .contact-band {
    position: absolute;
    left: 0;
    right: 0;
    bottom: 0;
    height: 182px;
    background: linear-gradient(180deg, var(--band-top) 0%, var(--band-bottom) 100%);
    border-top: 4px solid var(--acid);
    color: var(--ink-light);
  }
  .person {
    position: absolute;
    top: 20px;
    left: 30px;
    line-height: 1.3;
  }
  .person__name { font-weight: 600; font-size: 24px; color: var(--acid); }
  .person__role, .person__address { font-weight: 400; font-size: 18px; color: var(--ink-soft); }
  .social {
    position: absolute;
    top: 24px;
    right: 30px;
    display: flex;
    gap: 8px;
  }
  .social__square {
    width: 18px;
    height: 18px;
    border-radius: 2px;
    background: var(--acid);
  }
  .contact-lines {
    position: absolute;
    right: 30px;
    bottom: 22px;
    text-align: right;
    font-size: 18px;
    line-height: 1.35;
    list-style: none;
  }
  .contact-lines__label { font-weight: 600; margin-right: 6px; color: var(--acid); }
</style>
</head>
<body>
  <main class="sheet">
    <section class="card card--back" aria-label="Business card, reverse side">
      <div class="brand-disc" aria-hidden="true"></div>
      <p class="brand-name--back">Corvane Motion Limited</p>
    </section>

    <section class="card card--front" aria-label="Business card, front side">
      <div class="world-map" role="img" aria-label="Faint world map backdrop"></div>
      <p class="brand-name--front">Corvane Motion<br>Limited</p>

      <div class="contact-band">
        <div class="person">
          <p class="person__name">Owen Pritchard</p>
          <p class="person__role">Managing Director</p>
          <p class="person__address">14 Kestrel Drive<br>Brynmor, Cardiff CF99 4QX</p>
        </div>

        <div class="social" aria-label="Social profiles">
          <span class="social__square"></span>
          <span class="social__square"></span>
        </div>

        <ul class="contact-lines">
          <li><span class="contact-lines__label">P :</span>+44 (0)7582 913 406</li>
          <li><span class="contact-lines__label">E :</span>sales@corvanemotion.co.uk</li>
          <li><span class="contact-lines__label">W :</span>Corvanemotion.co.uk</li>
        </ul>
      </div>
    </section>
  </main>
</body>
</html>
```